Counselling practice needs a Business Card Design

I need a business card design for a new counselling practice in Canberra, Australia. The name of the practice is Dr Neil Hartwood, Counselling Services and the practice focuses on philosophical, narrative and existential counselling for individuals, couples and families. The final design should communicate professionalism, sophistication of analysis and psychological wholeness. The reverse side of the card should have an appointment reminder
Updates

Could the following qualifications also be included on card. BSc (Psychology), BA hons (Philosophy), PhD (Philosophy), Diploma of Community Counselling And the following affiliation Guidance and Wellbeing Society of Tarrin and Districts Inc. (GAWSOT) And my contact phone mobile phone number is 0478315942, and email is Neil.Hartwood347@mailbrook.example for inclusion as well.

Thank you all who have put in a design so far. I just wanted to clarify some design points based on what you have submitted. 1. The Guidance and Wellbeing Society. Tarrin and Districts Inc. (GAWSOT) is an affiliation only. 'Member of the Guidance and Wellbeing Society. Tarrin and Districts Inc (GAWSOT)' should appear with the same prominence of a qualification. 2. The Post Graduate Diploma in Community Counselling is a quaification and should appear as 'PG Dip (Community Counselling)' after the other qualifications. 3. I am advertising myself as a counsellor so 'Dr Neil Hartwood, Counselling Services' or 'Dr Neil Hartwood, Counsellor' is the equivalent of the business name. After looking at some of the designs I prefer Dr Neil Hartwood in sentence case rather than all capitals (DR NEIL HARTWOOD). 4. 'Philosophical, narrative and existential counselling for individuals, couples and families' is the description of the type of counselling services and should appear on the card.

One further point. I have updated my email address for the card. It is now drneilhartwood@tarringuidance.example

```html
<!DOCTYPE html>
<html lang="en">
<head>
<meta charset="utf-8">
<title>Dr Neil Hartwood, Counselling Services – Business Card</title>
<link rel="stylesheet" href="https://fonts.googleapis.com/css2?family=Crimson+Text:wght@400;600;700&display=swap">
<style>
  :root {
    --backdrop: #111111;
    --card: #ffffff;
    --ink: #1a1a1a;
    --rule: #2a2a2a;
  }
  * { box-sizing: border-box; margin: 0; padding: 0; }
  html, body {
    width: 1000px;
    height: 1200px;
    overflow: hidden;
    background: var(--backdrop);
  }
  body {
    position: relative;
    font-family: "Crimson Text", Georgia, serif;
    color: var(--ink);
  }
  .card {
    position: absolute;
    top: 469px;
    width: 462px;
    height: 262px;
    background: var(--card);
  }
  .card--front { left: 18px; }
  .card--back  { left: 517px; }

  /* Front */
  .front-block {
    position: absolute;
    left: 50%;
    top: 68px;
    transform: translateX(-50%);
    width: 300px;
  }
  .front-name {
    font-weight: 700;
    font-size: 28px;
    line-height: 1;
    text-align: center;
    letter-spacing: 0.2px;
    white-space: nowrap;
  }
  .front-tagline {
    font-size: 19.5px;
    line-height: 1;
    text-align: center;
    letter-spacing: 0.6px;
    margin-top: 2px;
    padding-bottom: 5px;
    border-bottom: 1.2px solid var(--rule);
    white-space: nowrap;
  }
  .front-credential {
    margin-top: 6px;
    line-height: 1.12;
  }
  .front-credential .lead { font-size: 13.5px; display: block; }
  .front-credential .sub  { font-size: 12.5px; display: block; }

  /* Back */
  .back-name {
    position: absolute;
    right: 18px;
    top: 20px;
    text-align: right;
  }
  .back-name .name {
    font-weight: 700;
    font-size: 22px;
    line-height: 1;
  }
  .back-name .role {
    font-size: 16px;
    line-height: 1.1;
  }
  .contact {
    position: absolute;
    left: 18px;
    top: 137px;
    list-style: none;
    font-size: 15px;
    line-height: 21px;
  }
  .contact li { display: flex; align-items: center; gap: 5px; }
  .contact svg { width: 11px; height: 11px; fill: var(--ink); }
  .back-rule {
    position: absolute;
    left: 10px;
    right: 10px;
    top: 186px;
    border-top: 1.2px solid var(--rule);
  }
  .back-details {
    position: absolute;
    left: 18px;
    right: 18px;
    top: 193px;
  }
  .qualifications {
    font-weight: 700;
    font-size: 13.5px;
    line-height: 1.2;
    display: flex;
    justify-content: space-between;
  }
  .qualifications .dot { font-size: 10px; }
  .practice-focus .lead { display: block; font-size: 15.5px; line-height: 1.15; }
  .practice-focus .sub  { display: block; font-size: 12.3px; line-height: 1.15; }
</style>
</head>
<body>
  <section class="card card--front" aria-label="Card front">
    <div class="front-block">
      <h1 class="front-name">DR NEIL HARTWOOD</h1>
      <p class="front-tagline">COUNSELLING SERVICES</p>
      <p class="front-credential">
        <span class="lead">Member of the Guidance and Wellbeing Society.</span>
        <span class="sub">Tarrin and Districts Inc (GAWSOT)</span>
      </p>
      <p class="front-credential">
        <span class="lead">The Post Graduate Diploma in Community</span>
        <span class="sub">Counselling (PG Dip - Community Counselling)</span>
      </p>
    </div>
  </section>

  <section class="card card--back" aria-label="Card back">
    <div class="back-name">
      <h2 class="name">Dr Neil Hartwood</h2>
      <p class="role">Counselling Services</p>
    </div>
    <ul class="contact">
      <li>
        <svg viewBox="0 0 12 12" aria-hidden="true"><path d="M1 4c0-2 2-3 5-3s5 1 5 3v1H8.5V3.8C8 3.3 7 3 6 3s-2 .3-2.5.8V5H1zM3 6h6l2 5H1z"/><circle cx="6" cy="8.3" r="1.2" fill="#fff"/></svg>
        <span>04.78.31.5942</span>
      </li>
      <li>
        <svg viewBox="0 0 12 12" aria-hidden="true"><path d="M0 2h12v8H0z"/><path d="M0.6 2.6 6 6.8l5.4-4.2M0.6 9.4 4.5 5.6M11.4 9.4 7.5 5.6" stroke="#fff" stroke-width="0.9" fill="none"/></svg>
        <span>drneilhartwood@tarringuidance.example</span>
      </li>
    </ul>
    <div class="back-rule"></div>
    <div class="back-details">
      <p class="qualifications">
        <span>BSc (Psychology)</span><span class="dot">●</span>
        <span>BA hons (Philosophy)</span><span class="dot">●</span>
        <span>PhD (Philosophy)</span>
      </p>
      <p class="practice-focus">
        <span class="lead">Counselling Services and the practice focuses on philosophical</span>
        <span class="sub">narrative and existential counselling for individuals, couples and families.</span>
      </p>
    </div>
  </section>
</body>
</html>
```